Create Design/GRAPHICS/TEXT FOR QUORVEL/E-COMMERCE PRODUCT

Hi,
I am looking for a designer to create a advertisement/images/text for a product that I sell on Quorvel.
The first attachment is a 3d rendering of the product that I sell and want to use as the main image of the design.
The second attachment is of a existing ad on Quorvel that you can use as a general idea of how I want the final graphic to look like.
The third and fourth attachments are of the text/graphics that I would like for you to include in the graphic.
Finally, the last attachment is my logo that I would like to include in the graphic.
Please feel free to get creative with this and if you have any questions please feel free to contact me.-
Update-I just added source files for logo as attachment six.
Thanks!
Target Market(s)
QUORVEL
Industry/Entity Type
Product
Look and feel

```html
<!DOCTYPE html>
<html lang="en">
<head>
<meta charset="utf-8">
<title>Hand Crafted BBQ Access Doors</title>
<link href="https://fonts.googleapis.com/css2?family=Open+Sans:ital,wght@0,400;0,600;0,700;1,400&display=swap" rel="stylesheet">
<style>
:root{
  --ink:#111111;
  --paper:#ffffff;
  --callout:#1e90ff;
  --steel-light:#e2e3e4;
  --steel-mid:#b9bbbd;
  --steel-dark:#8d9093;
}
*{margin:0;padding:0;box-sizing:border-box}
html,body{width:1200px;height:854px;overflow:hidden;background:var(--paper)}
body{position:relative;font-family:"Open Sans",Arial,sans-serif;color:var(--ink)}
.brand{position:absolute;left:78px;top:50px;display:flex;align-items:center;gap:10px}
.brand-mark{width:14px;height:14px;background:var(--ink)}
.brand-name{font-size:40px;font-weight:400;line-height:1;color:var(--ink)}
.headline{position:absolute;right:60px;top:20px;text-align:right}
.headline h1{font-size:31px;font-weight:600;line-height:1.1}
.headline .rule{position:absolute;right:0;top:44px;width:508px;height:3px;background:var(--ink)}
.headline p{margin-top:18px;font-size:25px;font-style:italic;line-height:1.1}
.product{position:absolute;left:48px;top:116px;width:572px;height:468px;
  background:linear-gradient(135deg,var(--steel-light),var(--steel-mid) 60%,var(--steel-dark))}
.callouts{position:absolute;left:0;top:0}
.feature{position:absolute;left:677px;font-size:18px;line-height:22px;white-space:nowrap}
.feature b{font-weight:700}
.feature .sub{display:block}
.badge{position:absolute;top:598px;width:126px;height:224px;border:2px solid var(--ink);background:var(--paper)}
.badge .art{height:122px;position:relative}
.badge .label{height:27px;border-top:2px solid var(--ink);font-size:12px;font-weight:600;text-align:center;line-height:25px}
.badge .note{position:absolute;left:0;right:0;bottom:0;height:73px;background:var(--ink);color:var(--paper);
  font-size:11px;font-weight:600;text-align:center;line-height:14px;padding-top:14px}
.badge svg{position:absolute;inset:0}
.stack{text-align:center;padding-top:8px}
.stack .small{font-size:11.5px;font-weight:600;line-height:14px}
.stack .big{font-size:38px;font-weight:700;line-height:40px}
.stack .bar{height:3px;background:var(--ink);margin:2px 10px}
.stack .tiny{font-size:9px;font-weight:600;line-height:12px}
</style>
</head>
<body>

<div class="brand">
  <span class="brand-mark"></span>
  <span class="brand-name">HALDEN</span>
</div>

<header class="headline">
  <h1>Hand Crafted BBQ Acess Doors</h1>
  <div class="rule"></div>
  <p>Elegant Design with Durable Construction</p>
</header>

<div class="product" role="img" aria-label="3D render of an open stainless steel double access door with paper towel holder and bar handle"></div>

<svg class="callouts" width="1200" height="600" aria-hidden="true">
  <g stroke="var(--callout)" stroke-width="2" fill="none">
    <line x1="548" y1="202" x2="668" y2="202"/>
    <line x1="548" y1="246" x2="668" y2="246"/>
    <line x1="548" y1="290" x2="668" y2="290"/>
    <polyline points="384,176 384,378 668,378"/>
    <line x1="548" y1="422" x2="668" y2="422"/>
    <polyline points="162,272 162,466 668,466"/>
  </g>
  <g fill="var(--callout)">
    <circle cx="668" cy="202" r="2.5"/><circle cx="668" cy="246" r="2.5"/>
    <circle cx="668" cy="290" r="2.5"/><circle cx="668" cy="378" r="2.5"/>
    <circle cx="668" cy="422" r="2.5"/><circle cx="668" cy="466" r="2.5"/>
  </g>
</svg>

<div class="feature" style="top:190px"><b>Premium grade</b>&nbsp; T-304 Stainless Steel Construction</div>
<div class="feature" style="top:235px"><b>Rugged</b> 16 gauge square frame construction</div>
<div class="feature" style="top:279px"><b>DOUBLE WALL</b> Construction
  <span class="sub">· 19 gauge outer wall</span>
  <span class="sub">· 20 gauge inner wall</span></div>
<div class="feature" style="top:367px"><b>Secure</b> 4 point magnectic closing system</div>
<div class="feature" style="top:411px"><b>High Quality</b> T-304 grade Stainless Steelhandles</div>
<div class="feature" style="top:455px"><b>Convenient</b> paper towel holder</div>

<section class="badge" style="left:266px">
  <div class="art">
    <svg width="122" height="122" viewBox="0 0 122 122">
      <defs>
        <path id="arcTop1" d="M31,56 A31,31 0 0 1 93,56"/>
        <path id="arcBot1" d="M33,70 A29,29 0 0 0 91,70"/>
      </defs>
      <circle cx="62" cy="56" r="43" fill="none" stroke="var(--ink)" stroke-width="3"/>
      <text font-size="8.5" font-weight="700"><textPath href="#arcTop1" startOffset="50%" text-anchor="middle">HANDCRAFTED</textPath></text>
      <rect x="10" y="44" width="104" height="24" fill="var(--ink)"/>
      <text x="62" y="61" fill="var(--paper)" font-size="12.5" font-weight="700" text-anchor="middle">HANDCRAFTED</text>
      <text font-size="7" font-weight="600" dy="6"><textPath href="#arcBot1" startOffset="50%" text-anchor="middle">with pride</textPath></text>
    </svg>
  </div>
  <div class="label">QUALITY</div>
  <div class="note">Our employes take<br>pride in their work</div>
</section>

<section class="badge" style="left:417px">
  <div class="art">
    <svg width="122" height="122" viewBox="0 0 122 122">
      <rect x="12" y="28" width="100" height="2" fill="var(--ink)"/>
      <rect x="12" y="33" width="100" height="2" fill="var(--ink)"/>
      <text x="62" y="60" font-size="12.5" font-weight="700" text-anchor="middle">DOUBLE WALL</text>
      <text x="62" y="76" font-size="12.5" font-weight="700" text-anchor="middle">CONSTRUCTION</text>
      <rect x="12" y="88" width="100" height="2" fill="var(--ink)"/>
      <rect x="12" y="93" width="100" height="2" fill="var(--ink)"/>
    </svg>
  </div>
  <div class="label">VALUE</div>
  <div class="note" style="padding-top:7px">Our doors weight<br>10 pounds more than<br>the competition</div>
</section>

<section class="badge" style="left:567px">
  <div class="art stack">
    <div class="small">PREMIUM GRADE</div>
    <div class="bar"></div>
    <div class="big">T-304</div>
    <div class="small">STRAINLESS STEEL</div>
    <div class="bar" style="margin-top:10px"></div>
  </div>
  <div class="label">STRENGHT</div>
  <div class="note">Offers higher level of<br>corrosion resistance</div>
</section>

<section class="badge" style="left:718px">
  <div class="art stack" style="padding-top:2px">
    <div class="big">16G</div>
    <div class="bar" style="margin:0 30px"></div>
    <div class="tiny">FRAME</div>
    <div class="bar" style="margin:3px 30px 0"></div>
    <div class="big">18G</div>
    <div class="bar" style="margin:0 30px"></div>
    <div class="tiny">OUTER WALL</div>
  </div>
  <div class="label">DURABILITY</div>
  <div class="note" style="padding-top:7px">Thick and Durable<br>Stainless Steel<br>construction</div>
</section>

<section class="badge" style="left:868px">
  <div class="art">
    <svg width="122" height="122" viewBox="0 0 122 122">
      <defs>
        <path id="arcTop5" d="M31,56 A31,31 0 0 1 93,56"/>
        <path id="arcBot5" d="M33,70 A29,29 0 0 0 91,70"/>
      </defs>
      <circle cx="62" cy="56" r="43" fill="none" stroke="var(--ink)" stroke-width="3"/>
      <text font-size="8.5" font-weight="700"><textPath href="#arcTop5" startOffset="50%" text-anchor="middle">SATISFACTION</textPath></text>
      <rect x="12" y="44" width="100" height="24" fill="var(--ink)"/>
      <text x="62" y="62" fill="var(--paper)" font-size="17" font-weight="700" text-anchor="middle">100%</text>
      <text font-size="7" font-weight="600" dy="6"><textPath href="#arcBot5" startOffset="50%" text-anchor="middle">Guaranteed</textPath></text>
    </svg>
  </div>
  <div class="label">PEACE OF MIND</div>
  <div class="note">Your satisfaction is<br>our highest goal</div>
</section>

</body>
</html>
```